Postcard Design Project A Healthy reminder

Dr.'s Dhelpit and Sirel dunwat. Internal Medicine/Family practice. This postcard will be for our patients that we have not seen in a while. Also we need another postcard (the one your designing) with a different heading for New patient's. Do you offer a price break for that? The only thing we would need to change is the heading. Please let me know. Thank you so much! Also can you use the map on the last postcard and our logo I made? I cant find it. Please feel free to call me or email me.

```html
<!DOCTYPE html>
<html lang="en">
<head>
<meta charset="utf-8">
<title>A Healthy Reminder – Postcard</title>
<link rel="stylesheet" href="https://fonts.googleapis.com/css2?family=Open+Sans:wght@300;400;600;700;800&display=swap">
<style>
  :root {
    --backdrop-top: #5d5d5d;
    --backdrop-bottom: #7a7a7a;
    --paper: #ffffff;
    --panel-light: #eeeeee;
    --brand-red: #a50c0c;
    --brand-red-bright: #c40d0d;
    --charcoal: #2a2b2c;
    --steel: #b9b9b9;
    --ink: #1d1d1d;
    --text-light: #ffffff;
  }
  html, body {
    margin: 0;
    padding: 0;
    width: 880px;
    height: 1200px;
    overflow: hidden;
  }
  body {
    background: linear-gradient(180deg, var(--backdrop-top), var(--backdrop-bottom));
    font-family: "Open Sans", Arial, sans-serif;
  }
  .postcard {
    position: absolute;
    display: block;
    box-shadow: 0 2px 6px rgba(0,0,0,.35);
  }
  .postcard--front { left: 48px; top: 54px; }
  .postcard--back  { left: 41px; top: 613px; }

  .brand-name { font: 700 15px "Open Sans", sans-serif; fill: var(--ink); }
  .brand-tagline { font: 700 8.5px "Open Sans", sans-serif; fill: var(--ink); letter-spacing: 1px; }
  .headline-lead { font: 300 29px "Open Sans", sans-serif; fill: var(--text-light); }
  .headline-lead strong, .headline-lead .em { font-weight: 800; }
  .headline-big { font: 800 77px "Open Sans", sans-serif; fill: var(--text-light); letter-spacing: -1px; }
  .contact-line { font: 400 16.5px "Open Sans", sans-serif; fill: var(--text-light); }
  .contact-phone { font: 700 27px "Open Sans", sans-serif; fill: var(--text-light); }

  .doctors-title { font: 400 29px "Open Sans", sans-serif; fill: var(--ink); }
  .doctors-title .name { font-weight: 800; fill: var(--brand-red); }
  .cta { font: 800 38px "Open Sans", sans-serif; fill: var(--text-light); }
  .social-label { font: 800 12px "Open Sans", sans-serif; fill: var(--text-light); }
  .social-url { font: 400 13px "Open Sans", sans-serif; fill: var(--text-light); }
  .social-url .handle { font-weight: 700; }
  .location-lead { font: 300 17px "Open Sans", sans-serif; fill: var(--text-light); }
  .location-detail { font: 800 16.5px "Open Sans", sans-serif; fill: var(--text-light); }
</style>
</head>
<body>

<!-- FRONT -->
<svg class="postcard postcard--front" width="784" height="533" viewBox="0 0 784 533" xmlns="http://www.w3.org/2000/svg">
  <defs>
    <linearGradient id="photoTone" x1="0" y1="0" x2="1" y2="1">
      <stop offset="0" stop-color="#e8dccf"/>
      <stop offset=".55" stop-color="#f3eee8"/>
      <stop offset="1" stop-color="#b9c3c2"/>
    </linearGradient>
    <linearGradient id="steelGrad" x1="0" y1="0" x2="0" y2="1">
      <stop offset="0" stop-color="#8d8d8d"/>
      <stop offset=".5" stop-color="#e2e2e2"/>
      <stop offset="1" stop-color="#9a9a9a"/>
    </linearGradient>
  </defs>

  <g class="info-panel">
    <rect class="panel-header" x="0" y="0" width="784" height="169" fill="var(--panel-light)"/>
    <rect class="panel-headline" x="0" y="169" width="784" height="220" fill="var(--brand-red)"/>
    <rect class="panel-contact" x="0" y="389" width="784" height="144" fill="var(--charcoal)"/>
  </g>

  <g class="curve-divider">
    <path d="M448 0 Q300 266 500 533" fill="none" stroke="var(--brand-red-bright)" stroke-width="26"/>
    <path d="M470 0 Q322 266 524 533" fill="none" stroke="url(#steelGrad)" stroke-width="14"/>
  </g>

  <path class="hero-photo" role="img" aria-label="Photo of two doctors in white coats reviewing a patient chart in a clinic hallway"
        d="M478 0 Q330 266 532 533 L784 533 L784 0 Z" fill="url(#photoTone)"/>

  <g class="brand-lockup">
    <rect x="56" y="96" width="12" height="12" fill="var(--brand-red)"/>
    <text class="brand-name" x="76" y="107">Dhelpit T. Dunwat, M.D.</text>
    <text class="brand-tagline" x="84" y="152">A Primary Care Office</text>
  </g>

  <g class="headline">
    <text class="headline-lead" x="50" y="218">A healthy <tspan class="em">reminder,</tspan></text>
    <text class="headline-lead" x="48" y="251">It is time for your</text>
    <text class="headline-big" x="46" y="311">annual</text>
    <text class="headline-big" x="46" y="372">exam.</text>
  </g>

  <g class="contact">
    <g class="icon-pin" fill="none" stroke="var(--text-light)" stroke-width="1.5">
      <circle cx="58" cy="403" r="4"/>
      <path d="M58 407 L58 414 M52 415 L64 415"/>
    </g>
    <text class="contact-line" x="71" y="420">4820 N. Alder Street Suite 210</text>
    <text class="contact-line" x="71" y="443">Marlow, Ca 93650</text>

    <g class="icon-phone" fill="none" stroke="var(--text-light)" stroke-width="1.6">
      <circle cx="65" cy="470" r="12"/>
      <path d="M60 463 Q58 466 61 472 Q65 478 70 477 L71 474 L67 472 L65 473 Q62 470 62 467 L63 465 L61 462 Z" fill="var(--text-light)" stroke="none"/>
    </g>
    <text class="contact-phone" x="89" y="480">(555) 014-7720</text>

    <g class="icon-web" fill="none" stroke="var(--text-light)" stroke-width="1.1">
      <circle cx="59" cy="503" r="6"/>
      <ellipse cx="59" cy="503" rx="2.6" ry="6"/>
      <path d="M53 503 H65"/>
    </g>
    <text class="contact-line" x="71" y="509">www.dhelpitdunwatmd.com</text>
  </g>
</svg>

<!-- BACK -->
<svg class="postcard postcard--back" width="797" height="541" viewBox="0 0 797 541" xmlns="http://www.w3.org/2000/svg">
  <defs>
    <clipPath id="leftPanel">
      <path d="M0 0 L318 0 Q478 230 287 541 L0 541 Z"/>
    </clipPath>
    <linearGradient id="mapTone" x1="0" y1="0" x2="1" y2="1">
      <stop offset="0" stop-color="#cfe6c4"/>
      <stop offset=".45" stop-color="#ececea"/>
      <stop offset="1" stop-color="#e3e6ea"/>
    </linearGradient>
    <linearGradient id="buildingTone" x1="0" y1="0" x2="0" y2="1">
      <stop offset="0" stop-color="#8c8a7f"/>
      <stop offset=".6" stop-color="#5f6558"/>
      <stop offset="1" stop-color="#7aa84c"/>
    </linearGradient>
    <linearGradient id="steelGradBack" x1="0" y1="0" x2="0" y2="1">
      <stop offset="0" stop-color="#8d8d8d"/>
      <stop offset=".5" stop-color="#e2e2e2"/>
      <stop offset="1" stop-color="#9a9a9a"/>
    </linearGradient>
  </defs>

  <rect class="card-paper" x="0" y="0" width="797" height="541" fill="var(--paper)"/>

  <g class="curve-divider">
    <path d="M340 0 Q500 230 310 541" fill="none" stroke="var(--brand-red-bright)" stroke-width="22"/>
    <path d="M326 0 Q488 230 298 541" fill="none" stroke="url(#steelGradBack)" stroke-width="12"/>
  </g>

  <g class="info-panel" clip-path="url(#leftPanel)">
    <rect x="0" y="0" width="420" height="122" fill="var(--panel-light)"/>
    <rect class="location-map" role="img" aria-label="Street map marking the office location" x="0" y="122" width="420" height="173" fill="url(#mapTone)"/>
    <rect x="0" y="295" width="420" height="106" fill="var(--brand-red)"/>
    <rect x="0" y="401" width="420" height="140" fill="var(--charcoal)"/>
  </g>

  <g class="office-photo">
    <circle cx="398" cy="320" r="98" fill="var(--brand-red)"/>
    <circle role="img" aria-label="Photo of the office building entrance with trees and lawn" cx="398" cy="320" r="88" fill="url(#buildingTone)"/>
  </g>

  <g class="doctors">
    <text class="doctors-title" x="40" y="62"><tspan class="name">Dr.'s Dhelpit</tspan> and</text>
    <text class="doctors-title" x="40" y="100"><tspan class="name">Sirel dunwat</tspan></text>
  </g>

  <g class="call-to-action">
    <text class="cta" x="39" y="339">CALL NOW</text>
    <text class="cta" x="37" y="378">(555) 014-7720</text>
  </g>

  <g class="social">
    <text class="social-label" x="40" y="435">VISIT US ON</text>
    <circle cx="135" cy="431" r="9" fill="#3b5ba0"/>
    <text class="social-url" x="40" y="457">www.facelink.com/<tspan class="handle">doctorsnearby</tspan></text>
  </g>

  <g class="location">
    <text class="location-lead" x="40" y="490">Located On The</text>
    <text class="location-detail" x="40" y="514">SE corner of Alder and Finch.</text>
  </g>

  <g class="mailing">
    <rect class="stamp-box" x="657" y="38" width="95" height="94" fill="none" stroke="#555" stroke-width="1"/>
    <line x1="548" y1="290" x2="752" y2="290" stroke="#333" stroke-width="1"/>
    <line x1="548" y1="338" x2="752" y2="338" stroke="#333" stroke-width="1"/>
    <line x1="548" y1="386" x2="752" y2="386" stroke="#333" stroke-width="1"/>
  </g>
</svg>

</body>
</html>
```